Verlindo Magician

I want the business card for my business to give to people who watch that later I will be employed to show magic here is my website http://www.balsamomagicien.com/I want the interesting design , i am very opened for formal and informal, I watch a lot of design so don't stick to the common shape and form but i hope it can also be produced the thing to write on will be the same as in picture that i will upload , i also will upload the logo for you that so can be easy to useDenis CostilleMagicianMAGICIAN BALSAMO 17 rue des Tilleuls - 25000 BESANÇON contact@verlindoillusions.example tel. 0381 946 157 tel. 0674 219 503

```html
<!DOCTYPE html>
<html lang="en">
<head>
<meta charset="utf-8">
<title>Verlindo Magician – Business Card</title>
<link href="https://fonts.googleapis.com/css2?family=Poppins:wght@300;400;700&display=swap" rel="stylesheet">
<style>
  :root {
    --stage: #e9e6e2;
    --brand-red: #ec2227;
    --ink: #111111;
    --paper: #ffffff;
    --pattern-grey: #efeeee;
    --pattern-pink: #f8eded;
    --figure-dark: #1b1b1b;
    --figure-mid: #3b3b3b;
  }
  * { box-sizing: border-box; margin: 0; padding: 0; }
  html, body {
    width: 1125px; height: 1200px; overflow: hidden;
    background: var(--stage);
    font-family: "Poppins", sans-serif;
  }
  .canvas { position: relative; width: 1125px; height: 1200px; }
  .card {
    position: absolute; left: 162px; width: 800px; height: 455px;
    box-shadow: 0 3px 8px rgba(0,0,0,.25);
    overflow: hidden;
  }
  .card--front { top: 110px; background: var(--paper); }
  .card--back { top: 660px; background: var(--paper); }

  .front__band {
    position: absolute; left: 0; top: 0; bottom: 0; width: 610px;
    background: var(--brand-red);
  }
  .front__portrait {
    position: absolute; left: 440px; top: 0; width: 350px; height: 455px;
    border-radius: 40px 0 0 0;
    border: 5px solid var(--paper);
    border-top: 0; border-right: 0;
    background: linear-gradient(180deg, var(--figure-mid), var(--figure-dark));
  }
  .front__details {
    position: absolute; left: 53px; top: 112px; color: var(--paper);
  }
  .front__name { font-weight: 700; font-size: 31px; line-height: 1.1; letter-spacing: .2px; }
  .front__role { font-size: 20px; font-weight: 400; line-height: 1.3; }
  .front__company { margin-top: 18px; font-size: 18px; line-height: 1.35; }
  .contact-list { list-style: none; margin-top: 12px; font-size: 18px; line-height: 25px; }
  .contact-list li { display: flex; align-items: center; gap: 10px; }
  .contact-list svg { width: 18px; height: 18px; flex: none; }

  .back__pattern {
    position: absolute; inset: 0;
    background: linear-gradient(135deg, var(--pattern-grey), var(--pattern-pink) 50%, var(--pattern-grey));
  }
  .back__portrait {
    position: absolute; left: 308px; top: 86px; width: 184px; height: 232px;
    border-radius: 24px 24px 8px 8px;
    background: linear-gradient(180deg, var(--figure-mid), var(--figure-dark));
  }
  .back__wordmark {
    position: absolute; left: 0; right: 0; top: 322px; text-align: center;
    font-size: 30px; font-weight: 300; color: var(--ink); letter-spacing: 1px;
  }
</style>
</head>
<body>
<main class="canvas">

  <section class="card card--front">
    <div class="front__band"></div>
    <div class="front__portrait" role="img" aria-label="Illustration of the magician in a dark jacket holding a playing card"></div>
    <div class="front__details">
      <h1 class="front__name">MARC RAVOULET</h1>
      <p class="front__role">Magician</p>
      <p class="front__company">MAGICIAN VERLINDO<br>17 rue des Tilleuls - 25000 BESANÇON</p>
      <ul class="contact-list">
        <li><svg viewBox="0 0 24 24" fill="#fff"><path d="M6.6 10.8a15.1 15.1 0 0 0 6.6 6.6l2.2-2.2c.3-.3.7-.4 1-.2 1.1.4 2.3.6 3.6.6.6 0 1 .4 1 1V20c0 .6-.4 1-1 1A17 17 0 0 1 3 4c0-.6.4-1 1-1h3.5c.6 0 1 .4 1 1 0 1.3.2 2.5.6 3.6.1.3 0 .7-.2 1z"/></svg>0381 946 157</li>
        <li><svg viewBox="0 0 24 24" fill="#fff"><path d="M6.6 10.8a15.1 15.1 0 0 0 6.6 6.6l2.2-2.2c.3-.3.7-.4 1-.2 1.1.4 2.3.6 3.6.6.6 0 1 .4 1 1V20c0 .6-.4 1-1 1A17 17 0 0 1 3 4c0-.6.4-1 1-1h3.5c.6 0 1 .4 1 1 0 1.3.2 2.5.6 3.6.1.3 0 .7-.2 1z"/></svg>0674 219 503</li>
        <li><svg viewBox="0 0 24 24"><rect x="3" y="6" width="18" height="12" fill="#fff"/><path d="M3 6l9 7 9-7" fill="none" stroke="#ec2227" stroke-width="1.6"/></svg>contact@verlindoillusions.example</li>
        <li><svg viewBox="0 0 24 24"><circle cx="12" cy="12" r="9" fill="#fff"/><path d="M7 9c2 0 3 1 3 3s2 2 2 4-1 3-1 3M14 4c0 2 2 2 3 3s0 3 2 3" fill="none" stroke="#ec2227" stroke-width="1.6"/></svg>www.verlindoillusions.example</li>
      </ul>
    </div>
  </section>

  <section class="card card--back">
    <div class="back__pattern" role="img" aria-label="Faint repeating pattern of playing-card suits in light grey and pink"></div>
    <div class="back__portrait" role="img" aria-label="Illustration of the magician holding a playing card"></div>
    <p class="back__wordmark">Verlindo Magician</p>
  </section>

</main>
</body>
</html>
```